MRT Property - Business Cards

Looking for a business card & general letterhead, signage etc design for our new logo.

Colours:
000a20
0056a2
00b5ef
0088ce
68cef2

Fonts:
Poppins
Karla

Please keep look and feel of new brand - example in the zip package I sent.

```html
<!DOCTYPE html>
<html lang="en">
<head>
<meta charset="utf-8">
<title>MRT Property – Stationery</title>
<link href="https://fonts.googleapis.com/css2?family=Poppins:wght@400;500;600;700&family=Karla:wght@400;500&display=swap" rel="stylesheet">
<style>
  :root{
    --ink:#000a20;
    --navy:#0056a2;
    --cyan:#00b5ef;
    --mid:#0088ce;
    --sky:#68cef2;
    --paper:#ffffff;
    --backdrop:#dcdcdc;
  }
  *{box-sizing:border-box;margin:0;padding:0}
  html,body{width:1200px;height:686px;overflow:hidden}
  body{background:var(--backdrop);font-family:"Poppins",sans-serif;color:var(--ink);position:relative}

  .sheet,.card{position:absolute;background:var(--paper);box-shadow:0 6px 18px rgba(0,0,0,.18);overflow:hidden}
  .edge-bands{position:absolute;inset:0;width:100%;height:100%}

  .brand{display:flex;align-items:center;gap:8px;font-family:"Poppins",sans-serif;font-weight:700;color:var(--navy);white-space:nowrap}
  .brand-dot{border-radius:50%;background:var(--navy);flex:none}

  /* Letterhead */
  .sheet{left:60px;top:33px;width:438px;height:620px}
  .sheet .brand{position:absolute;top:40px;right:36px;font-size:22px}
  .sheet .brand-dot{width:16px;height:16px}
  .sheet-contact{position:absolute;top:104px;right:36px;display:flex;gap:12px}
  .divider{width:1.5px;background:var(--mid)}
  .contact-list{list-style:none;font-size:8.5px;line-height:1.45;color:var(--ink)}
  .contact-list li{display:flex;gap:5px;align-items:flex-start}
  .contact-list svg{flex:none;margin-top:2px}

  /* Cards */
  .card{width:340px;height:200px;border-radius:10px;left:600px}
  .card-front{top:386px}
  .card-back{top:110px}
  .card-front .brand{position:absolute;left:50%;top:50%;transform:translate(-50%,-60%);font-size:28px}
  .card-front .brand-dot{width:20px;height:20px}

  .card-back .brand{position:absolute;left:30px;top:40px;font-size:18px}
  .card-back .brand-dot{width:13px;height:13px}
  .card-back .divider{position:absolute;left:188px;top:34px;height:80px}
  .person{position:absolute;left:204px;top:34px}
  .person-name{font-size:15px;font-weight:700;color:var(--navy);line-height:1.1}
  .person-name .surname{font-weight:400;color:var(--sky)}
  .person-role{font-family:"Karla",sans-serif;font-size:9px;color:var(--ink);margin-bottom:8px}
  .card-back .contact-list{font-size:7.5px}
  .card-address{position:absolute;left:30px;bottom:26px;font-size:7.5px;color:var(--ink)}
</style>
</head>
<body>

  <section class="sheet" aria-label="Letterhead">
    <svg class="edge-bands" viewBox="0 0 438 620" preserveAspectRatio="none" aria-hidden="true">
      <polygon points="0,370 9,370 9,560 22,620 0,620" fill="var(--sky)"/>
      <polygon points="14,560 22,560 40,612 438,612 438,620 22,620" fill="var(--navy)"/>
    </svg>
    <div class="brand"><span class="brand-dot"></span>MRT Property</div>
    <div class="sheet-contact">
      <span class="divider"></span>
      <ul class="contact-list">
        <li><svg width="7" height="9" viewBox="0 0 7 9"><path d="M3.5 0A3.5 3.5 0 0 0 0 3.5C0 6 3.5 9 3.5 9S7 6 7 3.5A3.5 3.5 0 0 0 3.5 0Z" fill="var(--mid)"/><circle cx="3.5" cy="3.5" r="1.3" fill="#fff"/></svg><span>Suite 3.14, Level 2<br>18 Harbourline Road<br>Riverton NSW 2150</span></li>
        <li><svg width="7" height="7" viewBox="0 0 8 8"><path d="M1.5 0 3 2 2.2 3A5 5 0 0 0 5 5.8L6 5l2 1.5L7 8C3 8 0 5 0 1Z" fill="var(--mid)"/></svg>+61 2 5550 0142</li>
        <li><svg width="7" height="7" viewBox="0 0 8 8"><circle cx="4" cy="4" r="3.4" fill="none" stroke="var(--mid)"/><path d="M.6 4h6.8M4 .6C2.5 2.5 2.5 5.5 4 7.4M4 .6C5.5 2.5 5.5 5.5 4 7.4" stroke="var(--mid)" fill="none" stroke-width=".7"/></svg>www.mrtproperty.com.au</li>
        <li><svg width="7" height="6" viewBox="0 0 8 6"><rect width="8" height="6" rx="1" fill="var(--mid)"/><path d="M0 .5 4 3.5 8 .5" stroke="#fff" stroke-width=".8" fill="none"/></svg>info@mrtproperty.com.au</li>
      </ul>
    </div>
  </section>

  <section class="card card-back" aria-label="Business card, contact side">
    <svg class="edge-bands" viewBox="0 0 340 200" preserveAspectRatio="none" aria-hidden="true">
      <polygon points="0,0 8,0 8,150 18,200 0,200" fill="var(--sky)"/>
      <polygon points="12,150 20,150 34,193 340,193 340,200 18,200" fill="var(--navy)"/>
    </svg>
    <div class="brand"><span class="brand-dot"></span>MRT Property</div>
    <span class="divider"></span>
    <div class="person">
      <p class="person-name">Callum <span class="surname">Reid</span></p>
      <p class="person-role">Director</p>
      <ul class="contact-list">
        <li><svg width="7" height="7" viewBox="0 0 8 8"><path d="M1.5 0 3 2 2.2 3A5 5 0 0 0 5 5.8L6 5l2 1.5L7 8C3 8 0 5 0 1Z" fill="var(--mid)"/></svg>+61 2 5550 0142</li>
        <li><svg width="7" height="7" viewBox="0 0 8 8"><circle cx="4" cy="4" r="3.4" fill="none" stroke="var(--mid)"/><path d="M.6 4h6.8M4 .6C2.5 2.5 2.5 5.5 4 7.4M4 .6C5.5 2.5 5.5 5.5 4 7.4" stroke="var(--mid)" fill="none" stroke-width=".7"/></svg>www.mrtproperty.com.au</li>
        <li><svg width="7" height="6" viewBox="0 0 8 6"><rect width="8" height="6" rx="1" fill="var(--mid)"/><path d="M0 .5 4 3.5 8 .5" stroke="#fff" stroke-width=".8" fill="none"/></svg>info@mrtproperty.com.au</li>
      </ul>
    </div>
    <p class="card-address">Suite 3.14, Level 2, 18 Harbourline Road, Riverton NSW 2150</p>
  </section>

  <section class="card card-front" aria-label="Business card, brand side">
    <svg class="edge-bands" viewBox="0 0 340 200" preserveAspectRatio="none" aria-hidden="true">
      <polygon points="0,0 8,0 8,150 18,200 0,200" fill="var(--sky)"/>
      <polygon points="12,150 20,150 34,193 340,193 340,200 18,200" fill="var(--navy)"/>
    </svg>
    <div class="brand"><span class="brand-dot"></span>MRT Property</div>
  </section>

</body>
</html>
```